Business Cards for company that supports physicians that do medical research

Need to create a business card for Qorvel Studies (www.qorvelstudies.example), a company devoted to supporting physicians who conduct medical research. The form of the card should match the message of research and information quest. I have provided the logo of the company as an uploaded file. Designs should be simple and slick aimed at very high end clients.

Target Market(s)

Medical doctors that are also researchers

Industry/Entity Type

Medical

Contact Information for Business Card

Should feature logo and fields for personal info:
Name/title
Phone /email

Font styles to use
Serif
Sans Serif

Requirements
Must have
• Qorvel logo and fields for personal info:
• Name: Bertrand Okonfu
• Title: VP Research and Senior Analyst
• Phone: 555-203-4719
• email: info@qorvelstudies.example
Nice to have
• Interesting cards that I've seen:
• 1- all black/charcoal or very dark background
• 2- Plastic - semi-transparent
• 3- non-standard height-width ratios
• 4- Functional cards -- USB drive incorporated
Should not have
• Too busy; needs to stay very simple

```html
<!DOCTYPE html>
<html lang="en">
<head>
<meta charset="utf-8">
<title>Qorvel Studies — Business Cards</title>
<link rel="stylesheet" href="https://fonts.googleapis.com/css2?family=Open+Sans:wght@400;600&display=swap">
<style>
  :root {
    --backdrop: #2b2b2c;
    --card: #1c1c1d;
    --card-edge: #303031;
    --green: #5cc84a;
    --blue: #2a8fd6;
    --white: #f2f2f2;
    --grey: #8a8a8a;
  }
  * { margin: 0; padding: 0; box-sizing: border-box; }
  html, body { width: 1200px; height: 900px; overflow: hidden; }
  body {
    background: var(--backdrop);
    font-family: "Open Sans", Arial, sans-serif;
    display: flex;
    align-items: center;
    justify-content: center;
    gap: 50px;
  }
  .card {
    width: 520px;
    height: 310px;
    background: var(--card);
    border: 1px solid var(--card-edge);
    border-radius: 24px;
    position: relative;
    box-shadow: 0 18px 40px rgba(0,0,0,0.45);
  }
  .brand {
    display: flex;
    align-items: center;
    gap: 12px;
    color: var(--green);
    font-weight: 600;
    white-space: nowrap;
  }
  .brand-dot {
    width: 14px; height: 14px;
    border-radius: 50%;
    background: var(--blue);
    flex: none;
  }

  /* Front: brand left, contact right */
  .card-front .brand {
    position: absolute;
    left: 34px;
    top: 132px;
    font-size: 27px;
  }
  .contact {
    position: absolute;
    left: 300px;
    top: 78px;
  }
  .contact-name {
    color: var(--green);
    font-weight: 600;
    font-size: 19px;
    line-height: 1.2;
  }
  .contact-title {
    color: var(--white);
    font-size: 12.5px;
    margin-top: 4px;
  }
  .contact-lines {
    list-style: none;
    margin-top: 40px;
  }
  .contact-lines li {
    display: flex;
    align-items: center;
    gap: 10px;
    color: var(--white);
    font-size: 13px;
    margin-bottom: 9px;
  }
  .contact-icon {
    width: 15px; height: 15px;
    border-radius: 3px;
    background: var(--green);
    display: flex;
    align-items: center;
    justify-content: center;
    flex: none;
  }

  /* Back: centred brand and web address */
  .card-back {
    display: flex;
    flex-direction: column;
    align-items: center;
    justify-content: center;
  }
  .card-back .brand { font-size: 38px; }
  .web {
    color: var(--blue);
    font-size: 13px;
    margin-top: 16px;
  }
</style>
</head>
<body>
  <section class="card card-front" aria-label="Card front">
    <div class="brand"><span class="brand-dot"></span>Qorvel Studies</div>
    <div class="contact">
      <p class="contact-name">Bertrand Okonfu</p>
      <p class="contact-title">VP Research and Senior Analyst</p>
      <ul class="contact-lines">
        <li>
          <span class="contact-icon">
            <svg width="11" height="11" viewBox="0 0 24 24" aria-hidden="true"><path fill="#1c1c1d" d="M6.6 10.8a15.1 15.1 0 0 0 6.6 6.6l2.2-2.2c.3-.3.7-.4 1-.2 1.1.4 2.3.6 3.6.6.6 0 1 .4 1 1V20c0 .6-.4 1-1 1A17 17 0 0 1 3 4c0-.6.4-1 1-1h3.5c.6 0 1 .4 1 1 0 1.3.2 2.5.6 3.6.1.3 0 .7-.2 1z"/></svg>
          </span>
          555-203-4719
        </li>
        <li>
          <span class="contact-icon">
            <svg width="11" height="11" viewBox="0 0 24 24" aria-hidden="true"><path fill="#1c1c1d" d="M3 5h18v14H3z"/><path fill="none" stroke="#5cc84a" stroke-width="2" d="M3 6l9 7 9-7"/></svg>
          </span>
          info@qorvelstudies.example
        </li>
      </ul>
    </div>
  </section>

  <section class="card card-back" aria-label="Card back">
    <div class="brand"><span class="brand-dot"></span>Qorvel Studies</div>
    <p class="web">www.qorvelstudies.example</p>
  </section>
</body>
</html>
```